Smile club flyer design

I am launching an office smile club and would like a design that sits my branding and that is appealing to customers. I have a design (I need a new one) that has all the information.
My website is maplehavendentalcarekx.com
Brand color is green. The design can be any color

Target Market(s)

Ages 30+

Industry/Entity Type

Dental

Font styles to use
Serif

Requirements
Must have
• Appealing to patients

```html
<!DOCTYPE html>
<html lang="en">
<head>
<meta charset="UTF-8">
<title>Smile Club Membership Flyer</title>
<link href="https://fonts.googleapis.com/css2?family=Poppins:wght@500;600;700;800&family=Barlow+Condensed:wght@500;600&family=Playfair+Display:wght@700&family=Dancing+Script:wght@700&display=swap" rel="stylesheet">
<style>
:root{
  --stage:#383838;
  --mint-1:#dcefe0;
  --mint-2:#b9e0c6;
  --brand-green:#0f7a3c;
  --band-green:#2f8f56;
  --dark-green:#0a4a25;
  --ink:#2d2d2d;
  --teal:#02a985;
  --teal-box:#04c298;
  --teal-body:#8fdcc3;
  --teal-text:#0b5a49;
  --gold:#d9a058;
  --gold-box:#f7b25c;
  --gold-body:#e6c79b;
  --gold-text:#6b4412;
  --gold-tick:#e3972f;
  --blue:#1a7cf0;
  --blue-box:#3e93f6;
  --blue-body:#9fc8f7;
  --blue-text:#153f86;
  --refresh-head:#063f1f;
  --refresh-box:#0ec752;
  --refresh-body:#86ebbe;
  --orange:#ee8a12;
  --white:#ffffff;
}
*{margin:0;padding:0;box-sizing:border-box}
html,body{width:1011px;height:1200px;overflow:hidden;background:var(--stage)}
.flyer{
  position:absolute;left:173px;top:101px;width:665px;height:998px;overflow:hidden;
  background:
    radial-gradient(ellipse 260px 200px at 90px 40px,rgba(255,255,255,.55),transparent 70%),
    radial-gradient(ellipse 300px 260px at 560px 120px,rgba(255,255,255,.35),transparent 70%),
    linear-gradient(180deg,var(--mint-1),var(--mint-2) 55%,#cbe9d4);
  font-family:'Poppins',sans-serif;
}
.abs{position:absolute}
.portrait{left:171px;top:0;width:335px;height:160px;
  background:radial-gradient(ellipse 80px 95px at 50% 45%,#e9b79a,#c8683a 70%,transparent 100%);
  border-radius:40% 40% 0 0/50% 50% 0 0}
.brand{left:420px;top:44px;width:240px;text-align:center;color:var(--brand-green)}
.brand-name{font-family:'Playfair Display',serif;font-weight:700;font-size:36px;line-height:38px}
.brand-sub{font-family:'Poppins',sans-serif;font-weight:700;font-size:14px;letter-spacing:6px;line-height:18px}
.intro{left:16px;top:98px;font-family:'Dancing Script',cursive;font-weight:700;font-size:40px;color:var(--dark-green)}
.title-band{left:58px;top:156px;width:549px;height:105px;background:var(--band-green);
  border-radius:22px 46px 8px 40px;display:flex;align-items:center;justify-content:center;
  box-shadow:0 4px 10px rgba(0,60,20,.25)}
.title-band h1{font-weight:800;font-size:80px;color:var(--white);letter-spacing:1px;line-height:1;margin-top:4px}
.membership{left:0;width:665px;top:272px;text-align:center;font-weight:800;font-size:50px;color:var(--brand-green);line-height:52px}
.tagline{left:0;width:665px;top:331px;text-align:center;font-weight:600;font-size:14.5px;color:var(--ink)}
.plan{position:absolute;top:368px;width:183px;height:296px}
.plan-body{position:absolute;left:6px;right:6px;top:120px;bottom:0;border-radius:0 0 12px 12px;border:2px solid rgba(255,255,255,.8);box-shadow:0 0 10px rgba(255,255,255,.6)}
.plan-head{position:absolute;left:0;top:0;width:183px;height:154px;border-radius:10px 10px 0 0;
  clip-path:polygon(0 0,100% 0,100% 89%,50% 100%,0 89%);text-align:center;color:var(--white)}
.plan-name{font-weight:700;font-size:23px;line-height:24px;margin-top:20px}
.plan-type{font-weight:500;font-size:15px;line-height:18px}
.price{position:absolute;left:22px;top:72px;width:138px;height:57px;border-radius:6px;text-align:center}
.price b{display:block;font-weight:800;font-size:38px;line-height:40px;text-shadow:0 2px 3px rgba(0,0,0,.25)}
.price small{display:block;font-size:12px;line-height:12px;margin-top:-2px}
.features{position:absolute;left:18px;right:6px;list-style:none;font-family:'Barlow Condensed',sans-serif;font-weight:600;font-size:11.5px;line-height:12.5px}
.features li{position:relative;padding-left:13px;margin-bottom:9px}
.check{position:absolute;left:0;top:2px;width:9px;height:9px;border-radius:50%}
.check::after{content:"";position:absolute;left:3px;top:1.5px;width:2px;height:4px;border:solid #fff;border-width:0 1.5px 1.5px 0;transform:rotate(45deg)}
.core{left:42px}.core .plan-head{background:var(--teal)}.core .price{background:var(--teal-box)}
.core .plan-body{background:var(--teal-body)}.core .features{color:var(--teal-text);top:184px}.core .check{background:var(--teal)}
.bright{left:244px}.bright .plan-head{background:var(--gold)}.bright .price{background:var(--gold-box)}
.bright .plan-body{background:var(--gold-body)}.bright .features{color:var(--gold-text);top:184px}.bright .check{background:var(--gold-tick)}
.total{left:448px}.total .plan-head{background:var(--blue)}.total .price{background:var(--blue-box)}
.total .plan-body{background:var(--blue-body)}.total .features{color:var(--blue-text);top:173px}.total .check{background:var(--blue)}
.join-band{left:0;top:695px;width:665px;height:127px;background:linear-gradient(90deg,rgba(255,255,255,.92),#fff 20%)}
.join{left:40px;top:716px;font-family:'Playfair Display',serif;font-weight:700;font-size:33px;color:var(--dark-green);line-height:44px}
.phone{left:72px;top:761px;font-family:'Playfair Display',serif;font-weight:700;font-size:43px;color:var(--orange);line-height:50px}
.refresh{left:449px;top:688px}
.refresh .plan-head{background:var(--refresh-head);height:153px}
.refresh .plan-body{background:var(--refresh-body);top:130px}
.refresh .price{background:var(--refresh-box)}
.refresh .plan-name{margin-top:18px;font-size:23px}
.refresh .plan-type{font-size:15.5px}
.refresh .features{top:168px;font-size:15px;line-height:15px;color:var(--dark-green)}
.refresh .features li{padding-left:14px;margin-bottom:7px}
.refresh .check{background:var(--orange);top:3px}
.new-tag{position:absolute;right:0;top:0;width:75px;height:56px;overflow:hidden;border-top-right-radius:10px}
.new-tag::before{content:"";position:absolute;inset:0;background:var(--orange);clip-path:polygon(0 0,100% 0,100% 100%)}
.new-tag span{position:absolute;right:4px;top:10px;font-family:'Playfair Display',serif;font-weight:700;font-size:18px;color:var(--white);transform:rotate(38deg)}
.offer{position:absolute;left:0;right:0;top:233px;text-align:center;font-family:'Playfair Display',serif;font-weight:700;font-size:24px;line-height:27px;color:var(--dark-green)}
.financing{left:22px;top:851px;font-weight:600;font-size:21px;color:var(--ink)}
.partner{top:901px;display:flex;align-items:center;gap:6px;font-weight:600;font-size:19px;color:var(--ink)}
.partner i{display:block;width:14px;height:14px;border-radius:50%;background:var(--brand-green)}
.partner-a{left:48px}
.partner-b{left:215px}
.partner-b i{background:#e0584a}
.footnote{left:38px;top:950px;font-weight:500;font-size:14px;color:var(--dark-green)}
</style>
</head>
<body>
<main class="flyer">
  <div class="abs portrait" role="img" aria-label="Smiling woman pointing to her smile"></div>

  <div class="abs brand">
    <div class="brand-name">Maplehaven</div>
    <div class="brand-sub">DENTAL CARE</div>
  </div>

  <div class="abs intro">Introducing</div>
  <div class="abs title-band"><h1>SMILE CLUB</h1></div>
  <div class="abs membership">MEMBERSHIP</div>
  <div class="abs tagline">AFFORDABLE DENTAL CARE&nbsp; – NO INSURANCE REQUIRED</div>

  <section class="plan core">
    <div class="plan-body"></div>
    <div class="plan-head">
      <div class="plan-name">CORE CARE</div>
      <div class="plan-type">PREVENTIVE</div>
      <div class="price"><b>$39</b><small>/MONTH</small></div>
    </div>
    <ul class="features">
      <li><span class="check"></span>Comprehensive Annual Exam</li>
      <li><span class="check"></span>2 Professional Cleanings per Year</li>
      <li><span class="check"></span>Routine Bitewing X-rays</li>
      <li><span class="check"></span>10% Savings on Treatment</li>
    </ul>
  </section>

  <section class="plan bright">
    <div class="plan-body"></div>
    <div class="plan-head">
      <div class="plan-name">BRIGHT</div>
      <div class="plan-type">COSMETIC</div>
      <div class="price"><b>$59</b><small>/MONTH</small></div>
    </div>
    <ul class="features">
      <li><span class="check"></span>Annual In-Office Whitening<br>(Top &amp; Bottom)</li>
      <li><span class="check"></span>Custom Whitening Trays</li>
      <li><span class="check"></span>15% Savings on Elective Treatment</li>
    </ul>
  </section>

  <section class="plan total">
    <div class="plan-body"></div>
    <div class="plan-head">
      <div class="plan-name">TOTAL SMILE</div>
      <div class="plan-type">PERIODONTAL</div>
      <div class="price"><b>$89</b><small>/MONTH</small></div>
    </div>
    <ul class="features">
      <li><span class="check"></span>3-4 Perio Maintenance<br>Visits per Year</li>
      <li><span class="check"></span>1 Comprehensive Exam</li>
      <li><span class="check"></span>Diagnostic X-rays</li>
      <li><span class="check"></span>15% Savings on Restorative &amp;<br>Elective Care</li>
    </ul>
  </section>

  <div class="abs join-band"></div>
  <div class="abs join">Join Smile Club Today!</div>
  <div class="abs phone">865-555-0142</div>

  <section class="plan refresh">
    <div class="plan-body"></div>
    <div class="plan-head">
      <div class="plan-name">SMILE</div>
      <div class="plan-type">REFRESH PACKAGE</div>
      <div class="price"><b>$499</b></div>
    </div>
    <div class="new-tag"><span>New</span></div>
    <ul class="features">
      <li><span class="check"></span>Cleaning</li>
      <li><span class="check"></span>Comprehensive Exam</li>
      <li><span class="check"></span>Whitening</li>
    </ul>
    <div class="offer">Limited<br>Time Offer</div>
  </section>

  <div class="abs financing">FLEXIBLE FINANCING FOR TREATMENT</div>
  <div class="abs partner partner-a"><i></i>PayWell</div>
  <div class="abs partner partner-b"><i></i>Bloomfi</div>
  <div class="abs footnote">*$49 Lifetime Activation Fee (Non-Refundable)</div>
</main>
</body>
</html>
```